Boutique custom software development company needs new business card

Our nearly 20 year old custom software development company would like to better include the fact that we are now providing Bitcoin services. These new services are B2B include education (how to acquire and securely hold Bitcoin) and integrating Bitcoin payments into existing ecommerce sites or other existing systems. Please keep the card clean and simple. Attached is our current design and some other files. vextorial.com

Target Market(s)

businesses owners interested in long term relationship

Industry/Entity Type

Custom software development and Bitcoin

Contact Information for Business Card

Dale Parker, dale@vextorial.com, vextorial.com, (888) 555-VXTRL

Font styles to use
Other font styles liked:
• monospace

Requirements
Must have
• double-sided
Nice to have
• clean and simple
Should not have
• physical address

```html
<!DOCTYPE html>
<html lang="en">
<head>
<meta charset="utf-8">
<title>Vextorial — Business Card</title>
<link href="https://fonts.googleapis.com/css2?family=Montserrat:wght@400;500;700;800&display=swap" rel="stylesheet">
<style>
  :root {
    --orange: #f07c22;
    --blue: #3a73c0;
    --white: #ffffff;
    --ink: #4a4a4a;
    --backdrop: #e7e5e2;
  }
  * { box-sizing: border-box; margin: 0; padding: 0; }
  html, body {
    width: 1200px;
    height: 900px;
    overflow: hidden;
    background: var(--backdrop);
    font-family: "Montserrat", sans-serif;
  }
  .sheet {
    width: 1200px;
    height: 900px;
    display: flex;
    flex-direction: column;
    align-items: center;
    justify-content: center;
    gap: 40px;
  }
  .card {
    width: 640px;
    height: 366px;
    border-radius: 18px;
    box-shadow: 0 6px 18px rgba(0,0,0,0.18);
    position: relative;
    overflow: hidden;
  }

  /* Front */
  .card-front {
    background: var(--orange);
    display: flex;
    align-items: center;
    justify-content: center;
  }
  .brand {
    display: flex;
    flex-direction: column;
    align-items: flex-start;
    color: var(--white);
  }
  .brand-name {
    font-weight: 800;
    font-size: 70px;
    letter-spacing: 1px;
    line-height: 1;
    text-transform: uppercase;
  }
  .brand-tagline {
    font-weight: 500;
    font-size: 22px;
    letter-spacing: -0.3px;
    line-height: 1.25;
    margin-top: 6px;
    padding-left: 40px;
  }
  .brand-services {
    font-weight: 500;
    font-size: 15px;
    letter-spacing: 0.2px;
    margin-top: 4px;
    padding-left: 40px;
  }

  /* Back */
  .card-back {
    background: var(--white);
    display: flex;
    align-items: center;
    padding: 0 34px 0 40px;
  }
  .card-back .brand {
    color: var(--blue);
    flex: 0 0 auto;
    margin-top: 40px;
  }
  .card-back .brand-name { font-size: 44px; }
  .card-back .brand-tagline { font-size: 14px; padding-left: 24px; margin-top: 4px; }
  .card-back .brand-services { font-size: 11px; padding-left: 24px; margin-top: 2px; color: var(--orange); }
  .divider {
    width: 1.5px;
    height: 150px;
    background: var(--blue);
    margin: 0 24px 0 30px;
    flex: 0 0 auto;
  }
  .contact {
    color: var(--ink);
    font-size: 12.5px;
    line-height: 1.5;
  }
  .person-name {
    font-weight: 700;
    font-size: 22px;
    text-transform: uppercase;
    line-height: 1.1;
  }
  .person-first { color: var(--orange); }
  .person-last { color: var(--blue); }
  .person-title {
    text-transform: uppercase;
    font-size: 13px;
    margin-bottom: 8px;
  }
  .contact-line {
    display: flex;
    align-items: center;
    gap: 7px;
  }
  .contact-line svg {
    width: 11px;
    height: 11px;
    flex: 0 0 auto;
    stroke: var(--blue);
    fill: none;
    stroke-width: 1.6;
  }
  .web-accent { color: var(--blue); }
</style>
</head>
<body>
<main class="sheet">
  <section class="card card-front">
    <div class="brand">
      <span class="brand-name">Vextorial</span>
      <span class="brand-tagline">developer of custom applications</span>
      <span class="brand-services">&amp; Bitcoin education and payment integration</span>
    </div>
  </section>

  <section class="card card-back">
    <div class="brand">
      <span class="brand-name">Vextorial</span>
      <span class="brand-tagline">developer of custom applications</span>
      <span class="brand-services">&amp; Bitcoin services for business</span>
    </div>
    <div class="divider"></div>
    <div class="contact">
      <p class="person-name"><span class="person-first">Dale</span> <span class="person-last">Parker</span></p>
      <p class="person-title">Director</p>
      <p class="contact-line">
        <svg viewBox="0 0 12 12" aria-hidden="true"><path d="M3 1.5 L4.5 3.5 L3.6 4.6 Q4.8 7.2 7.4 8.4 L8.5 7.5 L10.5 9 L9.5 10.5 Q4 10 1.5 2.5 Z"/></svg>
        <span>(888) 555-VXTRL</span>
      </p>
      <p class="contact-line">
        <svg viewBox="0 0 12 12" aria-hidden="true"><rect x="1" y="2.5" width="10" height="7"/><path d="M1 2.5 L6 6.5 L11 2.5"/></svg>
        <span>dale@vextorial.com</span>
      </p>
      <p class="contact-line">
        <svg viewBox="0 0 12 12" aria-hidden="true"><circle cx="6" cy="6" r="4.8"/><ellipse cx="6" cy="6" rx="2" ry="4.8"/><path d="M1.2 6 H10.8"/></svg>
        <span>www.<span class="web-accent">vextorial</span>.com</span>
      </p>
    </div>
  </section>
</main>
</body>
</html>
```